Coastal waterside shopping complex needs a billboard sign

"Harbourne Court" is the name of a building which comprises 4 shops in a coastal waterside location. We need a 2440mm (Wide) x 1100mm (High) "Harbourne Court" billboard design that will fit with the coastal theme but is modern and contemporary, positioning the building as a high class mini shopping complex.

The photo below is for reference only. We only need a design for the "Harbourne Court" sign.

The end product will need to be an EPS scalable vector file.

Industry/Entity Type

Shopping

```html
<!DOCTYPE html>
<html lang="en">
<head>
<meta charset="utf-8">
<title>Harbourne Court – Building Sign</title>
<link href="https://fonts.googleapis.com/css2?family=Montserrat:wght@900&family=Open+Sans:wght@400&display=swap" rel="stylesheet">
<style>
  :root {
    --bg: #f2f0ec;
    --pie-blue: #379fd3;
    --salon-pink: #e0157c;
    --bait-green: #2fb34b;
    --harbour-teal: #1e86a8;
    --sky-light: #4cc3ee;
    --sky-deep: #2aa6d9;
    --title-white: #f4f6f8;
    --tenant-ink: #1c2830;
  }
  * { margin: 0; padding: 0; box-sizing: border-box; }
  html, body { width: 1200px; height: 1029px; overflow: hidden; background: var(--bg); }
  .canvas { position: relative; width: 1200px; height: 1029px; }

  .panel { position: absolute; display: flex; }
  .tenant-name {
    font-family: "Open Sans", sans-serif;
    font-weight: 400;
    color: var(--tenant-ink);
    font-size: 56px;
    line-height: 1;
    letter-spacing: 0.5px;
  }

  .pie-shop {
    left: 78px; top: 394px; width: 521px; height: 241px;
    background: var(--pie-blue);
    justify-content: center; align-items: flex-start;
    padding-top: 72px; padding-left: 20px;
  }

  .building-panel {
    left: 599px; top: 271px; width: 523px; height: 243px;
    background: var(--harbour-teal);
    overflow: hidden;
  }
  .coast-scene {
    position: absolute; left: 0; top: 0; width: 523px; height: 243px;
  }
  .building-name {
    position: absolute; left: 26px; top: 42px;
    font-family: "Montserrat", sans-serif;
    font-weight: 900;
    font-size: 58px;
    line-height: 1.12;
    color: var(--title-white);
    text-shadow: 2px 3px 4px rgba(0, 0, 0, 0.35);
    letter-spacing: -0.5px;
  }

  .hair-salon {
    left: 599px; top: 516px; width: 523px; height: 119px;
    background: var(--salon-pink);
    justify-content: center; align-items: center;
  }
  .bait-shop {
    left: 599px; top: 637px; width: 523px; height: 120px;
    background: var(--bait-green);
    justify-content: center; align-items: center;
    padding-left: 40px;
  }
</style>
</head>
<body>
  <main class="canvas">
    <div class="panel pie-shop"><span class="tenant-name">PIE SHOP</span></div>

    <div class="panel building-panel">
      <svg class="coast-scene" viewBox="0 0 523 243" role="img" aria-label="Coastal scene with sky, sea, palm islands and a sailboat">
        <defs>
          <linearGradient id="sky" x1="0" y1="0" x2="0" y2="1">
            <stop offset="0" stop-color="var(--sky-light)"/>
            <stop offset="1" stop-color="var(--sky-deep)"/>
          </linearGradient>
        </defs>
        <circle cx="430" cy="120" r="250" fill="url(#sky)"/>
      </svg>
      <div class="building-name">HARBOURNE<br>COURT</div>
    </div>

    <div class="panel hair-salon"><span class="tenant-name">HAIR SALON</span></div>
    <div class="panel bait-shop"><span class="tenant-name">BAIT SHOP</span></div>
  </main>
</body>
</html>
```